website re-design - the brickleaf studio

The Brickleaf Studio is an existing website that we built using a new zealand based online CMS tool which is quite flexible and accomodates custom designs. You can check it here: http://www.pagecrafter.example.nz/.

We have a logo already and the content on the website is OK.
The website can be found at www.thebrickleafstudio.example.au

mainly the homepage, but if the design is easily adapted to the other pages then, we will commission the winner to update these pages also.
Updates

Hi there,  I am uploading an image to be used as the main image on the homepage design,  so all submissions have the same image.

Target Market(s)

property developers, architects, builders, home buyers

Industry/Entity Type

Shop

Requirements
Must have
• Must utilise the existing CMS or at least be compatible to upload
Nice to have
• a promotional banner that can be turned off and on and changed as required as we offer different promotions over time.

```html
<!DOCTYPE html>
<html lang="en">
<head>
<meta charset="utf-8">
<title>The Brickleaf Studio – Architectural Scale Models</title>
<link href="https://fonts.googleapis.com/css2?family=Cabin:wght@400;500;600&family=Open+Sans:wght@400;600&display=swap" rel="stylesheet">
<style>
:root{
  --orange:#e8701c;
  --orange-light:#f59a4e;
  --orange-dark:#d35f0f;
  --text:#222;
  --muted:#555;
  --grey-band:#e9e9e9;
  --line:#d5d5d5;
  --white:#fff;
  --link:#d9651a;
  --bullet:#c8231f;
}
*{box-sizing:border-box;margin:0;padding:0}
html,body{width:896px;height:1200px;overflow:hidden;background:var(--white)}
body{position:relative;font-family:"Open Sans",Arial,sans-serif;color:var(--text)}
.abs{position:absolute}

/* header */
.site-header{left:0;top:0;width:896px;height:122px;background:linear-gradient(#fff,#f4f4f4)}
.brand{left:76px;top:20px;display:flex;align-items:center;gap:14px}
.brand-mark{width:118px;height:66px;background:var(--orange)}
.brand-text{font-family:"Cabin",sans-serif}
.brand-name{font-size:25px;font-weight:500;color:#555;letter-spacing:.3px;line-height:1}
.brand-tag{font-size:12.5px;color:var(--orange);letter-spacing:.6px;margin-top:4px;font-weight:500}
.search{left:700px;top:21px;width:116px;height:13px;border:1px solid #888;background:#fff}
.phone{left:664px;top:60px;display:flex;align-items:center;gap:10px;font-family:"Cabin",sans-serif;font-size:20px;color:#111}
.phone-icon{width:28px;height:26px;border-radius:5px;background:var(--orange);display:flex;align-items:center;justify-content:center}

/* nav */
.main-nav{left:0;top:122px;width:896px;height:36px;background:linear-gradient(#fdfdfd,#ececec);border-top:1px solid var(--line)}
.main-nav a{position:absolute;top:9px;font-family:"Cabin",sans-serif;font-size:12px;color:#111;text-decoration:none;font-weight:500}
.main-nav a.active{left:78px;top:2px;width:69px;height:30px;line-height:30px;text-align:center;background:var(--orange);color:#fff;border-radius:2px}

/* hero */
.hero{left:0;top:158px;width:896px;height:327px;background:linear-gradient(var(--orange) 0%,var(--orange-light) 45%,var(--orange) 100%)}
.hero-quote{left:71px;top:71px;font-family:"Cabin",sans-serif;font-size:19.5px;line-height:33px;color:#111}
.hero-btn{left:90px;top:193px;width:152px;height:37px;border-radius:4px;background:linear-gradient(#fafafa,#c9c9c9);font-family:"Cabin",sans-serif;font-size:14px;text-align:center;line-height:37px;color:#111;box-shadow:0 1px 2px rgba(0,0,0,.3)}
.hero-dots{left:186px;top:289px;display:flex;gap:2px}
.hero-dots span{width:18px;height:18px;border-radius:50%;background:#3a2210}
.hero-dots span.on{background:#fff}
.hero-frame{left:286px;top:6px;width:555px;height:315px;background:#fff;border-radius:4px;padding:5px}
.hero-photo{width:100%;height:100%;background:linear-gradient(160deg,#c7c9c4 0%,#9c9a94 40%,#5b6a4a 70%,#3a3d38 100%)}

.sub-band{left:0;top:485px;width:896px;height:40px;background:linear-gradient(#e4e4e4,#fff)}

/* sidebar */
.side-box{left:63px;width:204px;border:1px solid #cfcfcf;border-radius:4px;background:linear-gradient(#fff,#ececec)}
.side-head{position:absolute;left:4px;top:1px;width:195px;height:36px;background:linear-gradient(var(--orange-light),var(--orange-dark));border-radius:2px;font-family:"Cabin",sans-serif;font-size:15px;color:#111;padding-left:41px;line-height:36px}
.side-head i{position:absolute;left:8px;top:5px;width:26px;height:26px;border-radius:4px;background:#e8c98f}
.field{position:absolute;left:14px;width:176px;height:27px;border:1px solid #ccc;background:linear-gradient(#fafafa,#e8e8e8);font-size:10px;color:#444;padding:8px 12px}
.btn{position:absolute;background:var(--orange);border-radius:3px;font-family:"Cabin",sans-serif;font-weight:600;font-size:11.5px;color:#111;text-align:center;line-height:26px;height:26px}
.model-photo{position:absolute;left:3px;top:41px;width:196px;height:186px;border:1px solid #888;border-radius:5px;background:linear-gradient(180deg,#d9d3c9 0%,#eeece8 45%,#8a7a6a 70%,#c9c3b8 100%)}
.model-caption{position:absolute;left:0;top:232px;width:100%;text-align:center;font-size:12px;color:#111}
.model-text{position:absolute;left:21px;top:256px;width:170px;font-size:10px;line-height:14.5px;color:#111}

/* main */
.welcome{left:299px;top:518px;font-family:"Cabin",sans-serif;font-size:21px;color:#111;font-weight:400}
.welcome span{color:var(--orange)}
.intro{left:297px;top:556px;width:525px;font-size:11.5px;line-height:24px;color:#222}
.questions{left:292px;top:637px;width:538px;height:228px;background:linear-gradient(#e9e9e9,#fff);border-radius:3px}
.questions-lead{position:absolute;left:27px;top:15px;width:500px;font-size:11.5px;line-height:24px}
.questions ul{position:absolute;left:18px;top:81px;list-style:none;width:515px}
.questions li{position:relative;padding-left:21px;font-size:9.8px;line-height:13px;margin-bottom:11px}
.questions li::before{content:"»";position:absolute;left:0;top:0;width:12px;height:12px;border-radius:50%;background:var(--bullet);color:#fff;font-size:10px;line-height:11px;text-align:center}
.easy{left:310px;top:885px;font-size:9.8px}
.step{left:330px;display:flex;align-items:center;gap:10px;font-size:11.5px;color:var(--link)}
.step i{width:24px;height:24px;display:block}
.body-copy{left:310px;width:520px;font-size:9.8px;line-height:14.5px;color:#111}
.body-copy a{color:var(--link);text-decoration:none;font-size:11.5px}

/* footer */
.site-footer{left:0;top:1128px;width:896px;height:72px;background:linear-gradient(#fff,#e6e6e6);border-top:1px solid var(--line)}
.social{left:76px;top:34px;display:flex;gap:14px}
.social span{width:18px;height:18px;border-radius:2px;background:#3d6fb0}
.footer-links{left:477px;top:18px;font-size:9px;color:#111}
.footer-links span{margin:0 6px;color:#555}
.copyright{left:458px;top:45px;font-size:9px;color:#111}
</style>
</head>
<body>

<header class="abs site-header">
  <div class="abs brand">
    <div class="brand-mark"></div>
    <div class="brand-text">
      <div class="brand-name">THE BRICKLEAF STUDIO</div>
      <div class="brand-tag">ARCHITECTURAL SCALE MODELS</div>
    </div>
  </div>
  <div class="abs search"></div>
  <svg class="abs" style="left:818px;top:19px" width="14" height="16" viewBox="0 0 14 16"><circle cx="6" cy="6" r="4.5" fill="none" stroke="#666" stroke-width="1.5"/><line x1="9" y1="9.5" x2="13" y2="14" stroke="#666" stroke-width="2"/></svg>
  <div class="abs phone">
    <div class="phone-icon"><svg width="14" height="16" viewBox="0 0 14 16"><path d="M3 1h3l1 4-2 1.5c1 2.5 2 3.5 3.5 4.5L10 9l4 1v3c0 1-1 2-2 2C6 15 1 9 1 3c0-1 1-2 2-2z" fill="#fff"/></svg></div>
    (08) 5550 1474
  </div>
</header>

<nav class="abs main-nav">
  <a class="active" href="#">HOME</a>
  <a href="#" style="left:165px">GALLERY</a>
  <a href="#" style="left:246px">ORDER ONLINE</a>
  <a href="#" style="left:356px">GET A QUOTE</a>
  <a href="#" style="left:461px">3D VISUALISATION</a>
  <a href="#" style="left:589px">ABOUTS US</a>
  <a href="#" style="left:680px">SITE MAP</a>
  <a href="#" style="left:762px">CONTACT</a>
</nav>

<section class="abs hero">
  <p class="abs hero-quote">“ a picture’s worth a<br>thousand words...<br>a model says it all..."</p>
  <div class="abs hero-btn">CLICK HERE</div>
  <div class="abs hero-dots"><span></span><span class="on"></span><span></span><span></span></div>
  <div class="abs hero-frame"><div class="hero-photo" role="img" aria-label="Photo of a scale model of a residential housing development"></div></div>
</section>
<div class="abs sub-band"></div>

<aside class="abs side-box" style="top:523px;height:161px">
  <div class="side-head"><i></i>LOGIN</div>
  <div class="field" style="top:49px">User Name</div>
  <div class="field" style="top:82px">Password</div>
  <div class="btn" style="left:17px;top:121px;width:62px">Submit</div>
</aside>

<aside class="abs side-box" style="top:691px;height:369px">
  <div class="side-head"><i style="background:#a9cbe6"></i>Scale Model</div>
  <div class="model-photo" role="img" aria-label="Photo of a white 1:100 scale model of a house"></div>
  <div class="model-caption">1:100 House - Scale Model</div>
  <p class="model-text">Even when you choose very basic parameters for your model, the model conveys a clear idea about how the building will look....</p>
  <div class="btn" style="left:22px;top:324px;width:78px">View Details</div>
</aside>

<h1 class="abs welcome">Welcome to <span>THE BRICKLEAF STUDIO</span></h1>
<p class="abs intro">Getting an architectural model produced can be expensive and time consuming, but it can also add a lot of value to a project.&nbsp; A scale model lets everyone involved, get a very clear understanding of your building.</p>

<section class="abs questions">
  <p class="questions-lead">If you answered yes to any of the following questions, then you should be using the brickleaf studio.</p>
  <ul>
    <li>Are you undertaking a new apartment development or land development and need a model for council approval or marketing purposes?</li>
    <li>Are you getting a new house designed and built and need a clear understanding of how it will look?</li>
    <li>Are you an architect or building designer looking for a more affordable way to add to your service?</li>
    <li>Are you wanting to clarify in your own mind how your new building sits on its site?</li>
    <li>Are you looking to for a way to market your buildings in an effective and affordable format that everyone can relate to?</li>
  </ul>
</section>

<p class="abs easy">It's this easy</p>
<div class="abs step" style="top:908px">
  <i><svg width="24" height="24" viewBox="0 0 24 24"><rect x="2" y="3" width="20" height="14" fill="none" stroke="#222" stroke-width="2"/><rect x="0" y="18" width="24" height="3" fill="#222"/><path d="M7 7h10l-1 5H8z" fill="#222"/></svg></i>
  Order online or fill in the quote form.
</div>
<div class="abs step" style="top:951px">
  <i><svg width="24" height="30" viewBox="0 0 24 30"><rect x="5" y="2" width="14" height="26" fill="#5b8fc4"/><rect x="2" y="16" width="8" height="12" fill="#7cba5a"/></svg></i>
  We'll build your model and deliver it right to your door.
</div>

<p class="abs body-copy" style="top:999px">You can tailor your model to suit your project and budget needs.&nbsp; There are various add-ons such as a display case, internal walls, acrylic windows, people trees and cars and site contours as well as a scaled pricing structure based on the size of your building.</p>
<p class="abs body-copy" style="top:1057px">We have made the system very easy to use, so all you need to do is click your way to your new scale model.&nbsp; Just follow the prompts and away you go. <a href="#">Click here to order your model now.</a>&nbsp;&nbsp; Or <a href="#">Click here to get a quote.</a></p>

<footer class="abs site-footer">
  <div class="abs social"><span></span><span style="background:#5aaee0"></span><span style="background:#e8701c"></span><span style="background:#2b6aa8"></span><span style="background:#5aa55a"></span></div>
  <div class="abs footer-links">Privacy Policy<span>|</span>Terms<span>|</span>Sitemap<span>|</span>Contact</div>
  <div class="abs copyright">Copyright © 2011 www.thebrickleafstudio.example.com All rights reserved</div>
</footer>

</body>
</html>
```